Corporate Design Hochtemperaturdichtungen
Zielgruppe
Wir sind spezialisiert auf Hochtemperaturdichtungen für den Ofen- & Kaminbau (Ofendichtung).
Desweiteren finden unsere Dichtungen in der Industrie Anwendung (Industrieöfen - Heizkessel
- Lackier- und Trocknungsanlagen - Maschinen- und Anlagenbau)
Die Zielgruppe für unser Angebot von passgenauen Ofendichtungen ist primär der Privatkunde
sowie der Ofenbauer, Kaminstudio / Schornsteinfeger.
Aufgabenstellung
Ziel des Projektes ist die Entwicklung eines neuen Logos-, Visitenkartendesign und damit
verbunden ein Briefpapierdesign für den Brand Glutfalke.
Die Vistitenkarte soll um ein ca. 2x2cm vCard QR-Code ergänzt werden.
Farbwelten:
Für den Brand Glutfalke.de sehe wir tendenziell Feuerfarben :
- rot
- gelb
- orange
- blau
- grün
- grau/schwarz Töne
Bilderwelt:
Prinzipiell möchten wir hier keine Beschränkungen beim Design geben.
Es sollte aber eher ein klares Design sein. Insbesondere wird ein einprägsames Logo in Verbindung
mit dem Markennamen „Glutfalke“ gewünscht. Der Brand soll aber sehr sympathisch und
einprägsam wirken, Wärme und Gebörgenheit ausstrahlen.
Der Rabe sollte sich im neuen Design auch wiederfinden.
Im Idealfall ist das Logo auf einem S/W Laserdrucker druckbar.

```html
<!DOCTYPE html>
<html lang="de">
<head>
<meta charset="utf-8">
<title>Glutfalke – Corporate Design</title>
<link rel="stylesheet" href="https://fonts.googleapis.com/css2?family=Montserrat:wght@400;500;600;700&family=Roboto:wght@300;400&display=swap">
<style>
:root{
  --ink:#333136;
  --panel-dark:#323035;
  --panel-right:#3d3c40;
  --panel-grey:#c4c4c4;
  --paper:#ffffff;
  --accent:#f7d117;
  --muted:#8a8a8a;
}
*{box-sizing:border-box;margin:0;padding:0}
html,body{width:1200px;height:1050px;overflow:hidden;background:var(--paper)}
body{position:relative;font-family:"Montserrat",sans-serif;color:var(--ink)}
.panel{position:absolute}
.panel--white{left:0;top:0;width:500px;height:350px;background:var(--paper)}
.panel--grey{left:0;top:350px;width:500px;height:450px;background:var(--panel-grey)}
.panel--dark{left:0;top:800px;width:500px;height:250px;background:var(--panel-dark)}
.panel--right{left:500px;top:0;width:700px;height:1050px;background:var(--panel-right)}

.logo{position:absolute;display:flex;align-items:center;gap:6px;line-height:1}
.logo__dot{display:block;border-radius:50%;background:currentColor;flex:none}
.logo__name{font-family:"Montserrat",sans-serif;font-weight:600;letter-spacing:-.5px}
.logo--lg .logo__dot{width:24px;height:24px}
.logo--lg .logo__name{font-size:31px}
.logo--md .logo__dot{width:20px;height:20px}
.logo--md .logo__name{font-size:26px}
.logo--sm .logo__dot{width:17px;height:17px}
.logo--sm .logo__name{font-size:22px}
.logo--ink{color:var(--ink)}
.logo--accent{color:var(--accent)}
.logo--white{color:var(--paper)}

.tagline{position:absolute;font-family:"Montserrat",sans-serif;font-size:12.2px;font-weight:500;letter-spacing:.9px;line-height:14px;white-space:nowrap}
.tagline--ink{color:var(--ink)}
.tagline--white{color:var(--paper)}

.card{position:absolute;left:129px;width:241px;height:156px;box-shadow:0 3px 8px rgba(0,0,0,.18)}
.card--front{top:402px;background:var(--panel-dark)}
.card--back{top:591px;background:var(--paper)}
.card__marker{position:absolute;left:0;top:92px;width:7px;height:14px;background:#9a9a9a}
.card__person{position:absolute;left:20px;top:94px;font-size:6.2px;line-height:9px}
.card__name{font-weight:700;font-size:6.8px}
.card__addr{margin-top:5px}
.card__contact{position:absolute;left:142px;top:94px;list-style:none;font-size:5.6px}
.card__contact li{display:flex;align-items:center;gap:4px;height:10.2px}
.card__contact svg{width:7px;height:7px;flex:none}

.letter{position:absolute;left:553px;top:53px;width:594px;height:842px;background:var(--paper)}
.letter .logo{left:352px;top:35px}
.letter .tagline{left:352px;top:73px}
.letter__sender{position:absolute;left:73px;top:167px;font-size:5.4px;font-weight:500}
.letter__recipient{position:absolute;left:73px;top:181px;font-family:"Roboto",sans-serif;font-weight:300;font-size:10.2px;line-height:12px;font-style:normal}
.fold{position:absolute;left:0;width:14px;height:0;border-top:.8px solid var(--ink)}
.fold--upper{top:297px}
.fold--lower{top:595px}
.letter__footer{position:absolute;left:73px;top:750px;display:flex;font-size:6.8px}
.footer__col{list-style:none;padding:0 10px 0 15px;border-left:.8px solid #9a9a9a}
.footer__col:first-child{padding-left:0;border-left:none}
.footer__col li{height:13.8px;display:flex;align-items:center;white-space:nowrap}
.footer__col--contact{width:108px}
.footer__col--contact li{gap:7px}
.footer__col--contact svg{width:9px;height:9px;flex:none}
.footer__col--person{width:103px}
.footer__col--bank{width:151px}
.icon{fill:none;stroke:var(--muted);stroke-width:1.2;stroke-linecap:round;stroke-linejoin:round}
</style>
</head>
<body>

<section class="panel panel--white">
  <div class="logo logo--lg logo--ink" style="left:139px;top:152px"><span class="logo__dot"></span><span class="logo__name">GLUTFALKE</span></div>
  <p class="tagline tagline--ink" style="left:139px;top:189px">Dichtungen mit Wärme gemacht<br>für Ofen, Kamin und Kessel</p>
</section>

<section class="panel panel--grey"></section>

<article class="card card--front">
  <div class="logo logo--md logo--accent" style="left:33px;top:65px"><span class="logo__dot"></span><span class="logo__name">GLUTFALKE</span></div>
</article>

<article class="card card--back">
  <div class="logo logo--sm logo--ink" style="left:20px;top:37px"><span class="logo__dot"></span><span class="logo__name">GLUTFALKE</span></div>
  <span class="card__marker"></span>
  <div class="card__person">
    <p class="card__name">Max Mustermann</p>
    <p>Geschäftsführer</p>
    <p class="card__addr">Musterweg 13<br>54321 Musterdorf</p>
  </div>
  <ul class="card__contact">
    <li><svg viewBox="0 0 10 10"><path class="icon" d="M2 1.5l1.5 0 .8 2-1 .8a5 5 0 0 0 2.4 2.4l.8-1 2 .8v1.5A1 1 0 0 1 7.5 9 6.5 6.5 0 0 1 1 2.5a1 1 0 0 1 1-1z"/></svg>+49 (0)1234 5 67 89-0</li>
    <li><svg viewBox="0 0 10 10"><rect class="icon" x="3" y="1" width="4" height="8" rx=".6"/></svg>+49 (0)1234 5 67 89-50</li>
    <li><svg viewBox="0 0 10 10"><rect class="icon" x="1" y="4" width="8" height="4.5" rx=".5"/><rect class="icon" x="3" y="1.5" width="4" height="2.5"/></svg>+49 (0)123 4 56 78 90</li>
    <li><svg viewBox="0 0 10 10"><rect class="icon" x="1" y="2.5" width="8" height="5.5"/><path class="icon" d="M1 2.5l4 3 4-3"/></svg>info@glutfalke.de</li>
    <li><svg viewBox="0 0 10 10"><circle class="icon" cx="5" cy="5" r="4"/><path class="icon" d="M1 5h8M5 1c-2 2.5-2 5.5 0 8M5 1c2 2.5 2 5.5 0 8"/></svg>glutfalke.de</li>
  </ul>
</article>

<section class="panel panel--dark">
  <div class="logo logo--lg logo--accent" style="left:139px;top:99px"><span class="logo__dot"></span><span class="logo__name">GLUTFALKE</span></div>
  <p class="tagline tagline--white" style="left:139px;top:137px">Dichtungen mit Wärme gemacht<br>für Ofen, Kamin und Kessel</p>
</section>

<section class="panel panel--right">
  <div class="logo logo--md logo--white" style="left:260px;top:961px"><span class="logo__dot"></span><span class="logo__name">GLUTFALKE</span></div>
</section>

<article class="letter">
  <div class="logo logo--lg logo--ink"><span class="logo__dot"></span><span class="logo__name">GLUTFALKE</span></div>
  <p class="tagline tagline--ink">Dichtungen mit Wärme gemacht<br>für Ofen, Kamin und Kessel</p>
  <p class="letter__sender">Glutfalke | Musterweg 13 | 54321 Musterdorf</p>
  <address class="letter__recipient">Max Mustermann<br>Musterstr. 1<br>12345 Muster</address>
  <span class="fold fold--upper"></span>
  <span class="fold fold--lower"></span>
  <footer class="letter__footer">
    <ul class="footer__col footer__col--contact">
      <li><svg viewBox="0 0 10 10"><path class="icon" d="M2 1.5l1.5 0 .8 2-1 .8a5 5 0 0 0 2.4 2.4l.8-1 2 .8v1.5A1 1 0 0 1 7.5 9 6.5 6.5 0 0 1 1 2.5a1 1 0 0 1 1-1z"/></svg>+49 (0)1234 5 67 89-0</li>
      <li><svg viewBox="0 0 10 10"><rect class="icon" x="1" y="4" width="8" height="4.5" rx=".5"/><rect class="icon" x="3" y="1.5" width="4" height="2.5"/></svg>+49 (0)1234 5 67 89-50</li>
      <li><svg viewBox="0 0 10 10"><rect class="icon" x="1" y="2.5" width="8" height="5.5"/><path class="icon" d="M1 2.5l4 3 4-3"/></svg>info@glutfalke.de</li>
      <li><svg viewBox="0 0 10 10"><circle class="icon" cx="5" cy="5" r="4"/><path class="icon" d="M1 5h8M5 1c-2 2.5-2 5.5 0 8M5 1c2 2.5 2 5.5 0 8"/></svg>glutfalke.de</li>
    </ul>
    <ul class="footer__col footer__col--person">
      <li>MAX MUSTERMANN</li>
      <li>Geschäftsführer</li>
      <li>Musterweg 13</li>
      <li>54321 Musterdorf</li>
    </ul>
    <ul class="footer__col footer__col--bank">
      <li>Glutbank Nord</li>
      <li>IBAN: DE43 XXXX 0110 XXXX 0481 XX</li>
      <li>BIC: KRXXDE55XXX</li>
      <li>Geschäftsführer: Max Mustermann</li>
    </ul>
    <ul class="footer__col footer__col--legal">
      <li>Ust. ID: DE2XX9XX10X</li>
      <li>HRB 1XX4XX</li>
      <li>Amtsgericht Eichental</li>
      <li>Gesellschaftssitz: Lindenau</li>
    </ul>
  </footer>
</article>

</body>
</html>
```